Company identity deisgn should support 2 languages

I would like to get our company identity design
This includes the following only
Business Cards 2 languages Arabic and English
Email signature
Letterhead
Linkedin profile images
Attached is the logo in Ai format

Requirements
Must have
• For business card
Must have
Name and Adrees in arabic
Name and Address in english
You might use both side of the card
Should not have
• Any pictures other than the logo

```html
<!DOCTYPE html>
<html lang="en">
<head>
<meta charset="utf-8">
<title>Lumen Logic Systems — Letterhead</title>
<link rel="stylesheet" href="https://fonts.googleapis.com/css2?family=Questrial&family=Noto+Sans+Arabic:wght@400&display=swap">
<style>
  :root {
    --brand-blue: #1479c4;
    --brand-grey: #6d6e71;
    --ink: #2b2b2b;
    --ink-soft: #4a4a4a;
    --paper: #ffffff;
  }
  * { box-sizing: border-box; margin: 0; padding: 0; }
  html, body { width: 960px; height: 1200px; overflow: hidden; background: var(--paper); }
  body { font-family: "Questrial", Arial, sans-serif; color: var(--ink); }
  .letterhead { position: relative; width: 960px; height: 1200px; background: var(--paper); }

  .brand { position: absolute; left: 63px; top: 78px; display: flex; align-items: center; gap: 12px; }
  .brand-dot { width: 14px; height: 14px; border-radius: 50%; background: var(--brand-blue); }
  .brand-name { font-size: 25px; color: var(--brand-blue); letter-spacing: 0.5px; line-height: 1; }
  .brand-tag { position: absolute; left: 89px; top: 110px; width: 300px; font-family: "Noto Sans Arabic", sans-serif;
               font-size: 12px; color: var(--brand-grey); direction: rtl; text-align: right; letter-spacing: 1px; }

  .contact { position: absolute; left: 670px; top: 74px; list-style: none; font-size: 14px; color: var(--ink-soft); line-height: 19.5px; }
  .contact li { display: flex; align-items: center; gap: 9px; }
  .contact svg { width: 11px; height: 11px; fill: var(--brand-blue); flex: none; }

  .salutation { position: absolute; left: 87px; top: 352px; font-size: 24px; color: var(--ink); }

  .letter-body { position: absolute; left: 87px; top: 418px; width: 792px; font-size: 13px; line-height: 18.4px; color: var(--ink-soft); }
  .letter-body p + p { margin-top: 18px; }

  .closing { position: absolute; left: 87px; top: 800px; font-size: 13px; color: var(--ink-soft); }
  .signature { position: absolute; left: 87px; top: 835px; width: 125px; height: 75px;
               background: linear-gradient(180deg, #f4f4f4, #e9e9e9); border-radius: 4px; }

  .address { position: absolute; top: 1075px; font-size: 14px; line-height: 18px; color: var(--ink-soft); }
  .address-en { left: 55px; }
  .address-ar { right: 67px; font-family: "Noto Sans Arabic", sans-serif; direction: rtl; text-align: right; font-size: 13px; line-height: 22px; top: 1066px; }

  .footer-band { position: absolute; left: 0; top: 1142px; width: 960px; height: 27px; }
  .footer-url { position: absolute; left: 0; top: 1142px; width: 791px; height: 27px; display: flex; align-items: center;
                justify-content: center; font-size: 13px; letter-spacing: 3px; color: #fff; }
</style>
</head>
<body>
<main class="letterhead">
  <header>
    <div class="brand">
      <span class="brand-dot"></span>
      <span class="brand-name">LUMEN LOGIC SYSTEMS</span>
    </div>
    <div class="brand-tag">شركة أنظمة لومن لوجيك</div>

    <ul class="contact">
      <li><svg viewBox="0 0 24 24"><path d="M6.6 10.8a15.1 15.1 0 0 0 6.6 6.6l2.2-2.2c.3-.3.7-.4 1-.2 1.1.4 2.3.6 3.6.6.6 0 1 .4 1 1V20c0 .6-.4 1-1 1A17 17 0 0 1 3 4c0-.6.4-1 1-1h3.5c.6 0 1 .4 1 1 0 1.3.2 2.5.6 3.6.1.3 0 .7-.2 1z"/></svg>415-730-2184</li>
      <li><svg viewBox="0 0 24 24"><path d="M7 1h10a2 2 0 0 1 2 2v18a2 2 0 0 1-2 2H7a2 2 0 0 1-2-2V3a2 2 0 0 1 2-2zm0 3v14h10V4z"/></svg>415-730-6652</li>
      <li><svg viewBox="0 0 24 24"><path d="M6 2h12v6H6zM3 9h18a1 1 0 0 1 1 1v8h-4v4H6v-4H2v-8a1 1 0 0 1 1-1zm5 7v4h8v-4z"/></svg>415-730-9071</li>
      <li><svg viewBox="0 0 24 24"><path d="M2 5h20v14H2zm2 2v.5l8 5 8-5V7l-8 5z"/></svg>hello@lumenlogic.com</li>
    </ul>
  </header>

  <h1 class="salutation">Dear Mr. Harlow,</h1>

  <section class="letter-body">
    <p>Lorem ipsum dolor sit amet, consectetur adipiscing elit. Donec orci purus, luctus vitae dignissim eu, iaculis sed purus. Vivamus faucibus, ipsum nec aliquet viverra, leo mauris condimentum ligula, sit amet sagittis enim ligula quis arcu. Nam egestas tortor id nisi porttitor mattis. In tortor ante, ultricies in suscipit a, tempus non massa. Vivamus et auctor mi. Fusce vel massa nulla. Phasellus nec eros mauris, et scelerisque orci.</p>
    <p>Donec malesuada orci vitae nulla accumsan porta a id massa. Quisque accumsan iaculis magna sit amet fringilla. Maecenas consequat, magna eget tincidunt semper, odio nibh rutrum mi, id feugiat ante nisi eu risus. Vestibulum nunc orci, rhoncus a placerat in, ultricies in mi. Cras mattis varius eros, vel fringilla nisi suscipit eget. Quisque scelerisque sagittis nulla at porttitor.</p>
    <p>Sed id augue vitae urna euismod commodo aliquet a quam. Pellentesque arcu velit, cursus et malesuada ut, consequat et diam. Nullam erat sem, rhoncus id ullamcorper vitae, rhoncus et arcu. In ultricies ultricies nulla, ut rutrum nisi iaculis at. Donec eu magna a metus ornare faucibus. Fusce aliquet faucibus ultricies. Morbi semper, est id tincidunt gravida, sem arcu adipiscing lacus, ac bibendum nulla leo eu purus. Quisque nec diam sed risus consectetur a ccumsan quis quis nibh. Vestibulum id purus lorem.</p>
    <p>It is a long established fact that a reader will be distracted by the readable content of a page when looking at its layout. The point of using Lorem Ipsum is that it has a more-or-less normal distribution of letters, as opposed to using 'Content here, content here', making it look like readable English. Many desktop publishing packages</p>
  </section>

  <p class="closing">Sincerely,</p>
  <div class="signature" role="img" aria-label="Handwritten signature of the sender"></div>

  <footer>
    <address class="address address-en" style="font-style:normal">4120 Cedar Hollow Road<br>Fairbanks, Alaska 99701</address>
    <address class="address address-ar" style="font-style:normal">4120 طريق سيدار هولو<br>فيربانكس، ألاسكا 99701</address>

    <svg class="footer-band" viewBox="0 0 960 27" preserveAspectRatio="none" aria-hidden="true">
      <rect x="0" y="0" width="800" height="27" fill="var(--brand-blue)"/>
      <polygon points="791,27 805,0 960,0 960,27" fill="var(--brand-grey)"/>
    </svg>
    <div class="footer-url">WWW.LUMENLOGIC.COM</div>
  </footer>
</main>
</body>
</html>
```